The design should look similar to the uploaded example to accommodate the information needed for a business card template. I would like to see the colors orange and charcoal grey incorporated along with the logo.The following should be on the back of the card SPECIALIZING IN NEW AND USED TIRES & WHEELS FOR:- Loaders- Skid Steers- Telehandlers- Boom Lifts- Forklifs and moreELIMINATING DOWNTIMEWheel Exchange Program for New & Used Foam Filled and Solid Rubber TiresSPECIALTY SERVICES- Foam Filling Tires- Largest Tire Press in SE- ONSITE Forklift Tire Press- Boom Truck Services - Rubber Tracks

Target Market(s)

New and Existing Customers

Industry/Entity Type

Business

Contact Information for Business Card

NAMEHEAVY DUTY TIRE, LLC8470 Belvedere RoadWest Palm Beach, FL 33411P: 844-HD-TIRESF: 561-431-6469C:E: W: WWW.GRANITERIMSUPPLY-EXAMPLE.COM

Font styles to use
Sans Serif

Colors
f37122
333333

Requirements
Must have
• The logo and the information indicated for the backside of the card
Nice to have
• Keep the orange and charcoal grey colors

```html
<!DOCTYPE html>
<html lang="en">
<head>
<meta charset="utf-8">
<title>Granite Rim Supply, LLC – Business Card</title>
<link href="https://fonts.googleapis.com/css2?family=Roboto:wght@400;700;900&display=swap" rel="stylesheet">
<style>
  :root{
    --charcoal:#3d4d5a;
    --charcoal-dark:#2f3c47;
    --ink:#333333;
    --orange:#f37122;
    --paper:#ffffff;
    --stage:#e4e2de;
  }
  *{margin:0;padding:0;box-sizing:border-box}
  html,body{width:1200px;height:950px;overflow:hidden}
  body{background:var(--stage);font-family:"Roboto",Arial,sans-serif;color:var(--ink);
       display:flex;flex-direction:column;align-items:center;justify-content:center;gap:44px}
  .card{width:720px;height:412px;position:relative;overflow:hidden;box-shadow:0 6px 18px rgba(0,0,0,.18)}

  /* Back */
  .card--back{background:linear-gradient(120deg,var(--charcoal-dark),var(--charcoal) 60%,#4a5b68);color:#fff;padding:38px 44px}
  .brand{display:flex;align-items:center;gap:16px}
  .brand__mark{width:64px;height:64px;border-radius:50%;background:var(--orange);flex:none}
  .brand__name{font-weight:900;font-size:30px;line-height:1.05;letter-spacing:.5px;text-transform:uppercase}
  .card--back .brand{justify-content:center;margin-bottom:28px}
  .card--back .brand__name{color:#fff}
  .offer{margin-bottom:16px}
  .offer__title{font-weight:700;font-size:17px;letter-spacing:.4px;text-transform:uppercase}
  .offer__items{font-size:15px;margin-top:4px;color:#e8ecef}
  .dot{color:var(--orange);margin:0 6px}

  /* Front */
  .card--front{background:var(--paper)}
  .card--front .brand{position:absolute;top:52px;left:0;right:0;justify-content:center}
  .card--front .brand__name{color:var(--charcoal)}
  .band{position:absolute;top:168px;left:0;width:100%;height:96px;background:var(--charcoal)}
  .band__accent{position:absolute;top:0;right:0;width:150px;height:100%;background:var(--orange)}
  .band__seal{position:absolute;top:12px;right:116px;width:72px;height:72px;border-radius:50%;
              background:var(--charcoal-dark);border:4px solid var(--orange)}
  .person{position:absolute;top:20px;right:220px;text-align:left}
  .person__name{color:var(--orange);font-weight:700;font-size:24px;letter-spacing:1px}
  .person__role{color:#fff;font-size:16px;letter-spacing:1px;margin-top:2px}
  .contact{position:absolute;top:284px;right:40px;text-align:right;font-size:17px;line-height:1.6;color:#4a4a4a}
  .contact__line{display:flex;justify-content:flex-end;align-items:center;gap:14px}
  .contact__item{display:inline-flex;align-items:center;gap:6px}
  .icon{width:15px;height:15px;fill:var(--charcoal)}
</style>
</head>
<body>

<section class="card card--back" aria-label="Back of card">
  <div class="brand">
    <span class="brand__mark"></span>
    <span class="brand__name">Granite Rim<br>Supply, LLC</span>
  </div>
  <div class="offer">
    <p class="offer__title">Specializing in new and used tires &amp; wheels for</p>
    <p class="offer__items">Loaders<span class="dot">•</span>Skid Steers<span class="dot">•</span>Telehandlers<span class="dot">•</span>Boom Lifts<span class="dot">•</span>Forklifs and more</p>
  </div>
  <div class="offer">
    <p class="offer__title">Eliminating downtime</p>
    <p class="offer__items">Wheel Exchange Program for New &amp; Used Foam Filled and Solid Rubber Tires</p>
  </div>
  <div class="offer">
    <p class="offer__title">Specialty services</p>
    <p class="offer__items">Foam Filling Tires<span class="dot">•</span>Largest Tire Press in SE<span class="dot">•</span>ONSITE Forklift Tire Press<br>Boom Truck Services<span class="dot">•</span>Rubber Tracks</p>
  </div>
</section>

<section class="card card--front" aria-label="Front of card">
  <div class="brand">
    <span class="brand__mark"></span>
    <span class="brand__name">Granite Rim<br>Supply, LLC</span>
  </div>
  <div class="band">
    <div class="band__accent"></div>
    <div class="band__seal"></div>
    <div class="person">
      <p class="person__name">DANA WHITLOCK</p>
      <p class="person__role">PRESIDENT</p>
    </div>
  </div>
  <div class="contact">
    <p class="contact__line">5126 Marston Lane, West Palm Beach, FL 33411</p>
    <p class="contact__line">
      <span class="contact__item"><svg class="icon" viewBox="0 0 16 16"><path d="M3 1h3l1 4-2 1a9 9 0 0 0 5 5l1-2 4 1v3a2 2 0 0 1-2 2A13 13 0 0 1 1 3a2 2 0 0 1 2-2z"/></svg>844-GR-WHEEL</span>
      <span class="contact__item"><svg class="icon" viewBox="0 0 16 16"><rect x="4" y="0" width="8" height="16" rx="1.5"/><rect x="5.5" y="2" width="5" height="9" fill="#fff"/></svg>836 502 7718</span>
    </p>
    <p class="contact__line">
      <span class="contact__item"><svg class="icon" viewBox="0 0 16 16"><rect x="4" y="1" width="8" height="4"/><rect x="1" y="5" width="14" height="7" rx="1"/><rect x="4" y="10" width="8" height="5" fill="#fff" stroke="#3d4d5a"/></svg>561-278-9053</span>
      <span class="contact__item"><svg class="icon" viewBox="0 0 16 16"><rect x="1" y="3" width="14" height="10" rx="1"/><path d="M1.5 3.5 8 9l6.5-5.5" stroke="#fff" fill="none" stroke-width="1.3"/></svg>name@graniterim-example.com</span>
      <span class="contact__item"><svg class="icon" viewBox="0 0 16 16"><circle cx="8" cy="8" r="7"/><path d="M1 8h14M8 1c3 3 3 11 0 14M8 1c-3 3-3 11 0 14" stroke="#fff" fill="none" stroke-width="1"/></svg>graniterimsupply-example.com</span>
    </p>
  </div>
</section>

</body>
</html>
```